Business Card Design - Property Management & Real Estate Services

I need a business card design for my company that I can print ZEPLA Cards. The company is called Brindle Management Company. It is a property management and real estate company. The design has to be clean and modern. I need two versions. One for my employee and one for me. However, the design will be the same, just different text. You can get a feel for the company by looking at our website at www.brindlemanagement.example.

Industry/Entity Type

Property Management

Contact Information for Business Card

I will be using ZEPLA.com to print my cards. I will most likely use the rounded edges card. I need two versions, however, they will be the same design. I need one for me and my employee.

Colors
3276b5
33a6d7

Requirements
Must have
• Company Logo
• Name of person
• Property Management & Real Estate Service
• Phone
• Email
• Website
• Address
• A space to place a QR code

```html
<!DOCTYPE html>
<html lang="en">
<head>
<meta charset="utf-8">
<title>Brindle Management – Business Card</title>
<link rel="stylesheet" href="https://fonts.googleapis.com/css2?family=Roboto:ital,wght@0,300;0,400;0,500;1,700&display=swap">
<style>
  :root {
    --backdrop: #4a4b4d;
    --card: #1d1e22;
    --silver: #b9bcc2;
    --brand-blue: #3276b5;
    --contact-blue: #3a86d0;
    --muted-text: #c9ccd2;
  }
  * { margin: 0; padding: 0; box-sizing: border-box; }
  html, body {
    width: 799px;
    height: 1200px;
    overflow: hidden;
    background: var(--backdrop);
    font-family: "Roboto", Arial, sans-serif;
  }
  .sheet {
    width: 799px;
    height: 1200px;
    display: flex;
    flex-direction: column;
    align-items: center;
    justify-content: space-around;
    padding: 60px 0;
  }
  .card {
    position: relative;
    width: 640px;
    height: 366px;
    background: var(--card);
    border-radius: 26px;
    overflow: hidden;
  }

  /* Front */
  .card-front {
    display: flex;
    align-items: center;
    justify-content: center;
  }
  .wordmark {
    text-align: center;
    color: var(--silver);
    font-weight: 400;
    margin-top: 30px;
  }
  .wordmark .name {
    display: block;
    font-size: 72px;
    letter-spacing: 5px;
    line-height: 1;
  }
  .wordmark .sub {
    display: block;
    font-size: 15px;
    letter-spacing: 14px;
    margin-top: 10px;
    padding-left: 14px;
  }

  /* Back */
  .back-brand {
    position: absolute;
    left: 40px;
    top: 38px;
    color: var(--brand-blue);
    font-weight: 400;
    display: flex;
    align-items: center;
    gap: 14px;
  }
  .back-brand .mark-square {
    width: 40px;
    height: 40px;
    background: var(--brand-blue);
  }
  .back-brand .name {
    display: block;
    font-size: 46px;
    letter-spacing: 3px;
    line-height: 1;
  }
  .back-brand .sub {
    display: block;
    font-size: 11px;
    letter-spacing: 10px;
    margin-top: 4px;
  }
  .brand-rule {
    position: absolute;
    left: 40px;
    top: 116px;
    width: 360px;
    height: 2px;
    background: var(--brand-blue);
  }
  .person {
    position: absolute;
    left: 40px;
    top: 128px;
  }
  .person-name {
    color: var(--brand-blue);
    font-size: 23px;
    font-weight: 700;
    font-style: italic;
  }
  .person-role {
    color: var(--muted-text);
    font-size: 15px;
    font-weight: 300;
    margin-top: 2px;
  }
  .contacts {
    position: absolute;
    left: 40px;
    top: 214px;
    list-style: none;
    color: var(--contact-blue);
    font-size: 17px;
    font-weight: 400;
    line-height: 28px;
  }
  .contacts li {
    display: flex;
    align-items: center;
    gap: 10px;
  }
  .contacts svg {
    width: 14px;
    height: 14px;
    flex: none;
  }
</style>
</head>
<body>
<main class="sheet">

  <section class="card card-front" aria-label="Card front">
    <div class="wordmark">
      <span class="name">BRINDLE</span>
      <span class="sub">MANAGEMENT</span>
    </div>
  </section>

  <section class="card card-back" aria-label="Card back">
    <div class="back-brand">
      <span class="mark-square"></span>
      <div>
        <span class="name">BRINDLE</span>
        <span class="sub">MANAGEMENT</span>
      </div>
    </div>
    <div class="brand-rule"></div>

    <div class="person">
      <p class="person-name">Mateo R. Alvarez</p>
      <p class="person-role">Founder</p>
    </div>

    <ul class="contacts">
      <li>
        <svg viewBox="0 0 16 16" aria-hidden="true"><path fill="currentColor" d="M3.6 1.5l2.3 2.6-1.3 1.9c.9 2 2.5 3.6 4.5 4.5l1.9-1.3 2.6 2.3-1.4 2.5C6.6 13.8 2.2 9.4 1.1 3z"/></svg>
        (555) 010-4827
      </li>
      <li>
        <svg viewBox="0 0 16 16" aria-hidden="true"><rect x="1" y="3" width="14" height="10" fill="currentColor"/><path d="M1.5 3.5L8 9l6.5-5.5" fill="none" stroke="#1d1e22" stroke-width="1.4"/></svg>
        mateo@brindlemanagement.example
      </li>
      <li>
        <svg viewBox="0 0 16 16" aria-hidden="true"><circle cx="8" cy="8" r="6.5" fill="none" stroke="currentColor" stroke-width="1.6"/><path d="M1.5 8h13M8 1.5c-3 3.5-3 9.5 0 13M8 1.5c3 3.5 3 9.5 0 13" fill="none" stroke="currentColor" stroke-width="1.2"/></svg>
        www.brindlemanagement.example
      </li>
      <li>48 Harbor Lane #210 Lakeview, FL 30000</li>
    </ul>
  </section>

</main>
</body>
</html>
```